Automotive eCommerce Business looking for a business card design

Looking for a clean and simple business card design. Our company name is "Brindle Auto" and we are a company specializing in the ecommerce sales of automotive parts, specifically for pick up trucks and large SUVs. Our company colours are red, black, and white.

Feel free to use the logo provided or create a new logo that you seem fit. Looking forward to your creative ideas!

Industry/Entity Type

Automotive

Contact Information for Business Card

We were thinking of a possibly two-sided design featuring just the logo and company name on one side, and personal information on the other side. Single sided designs will be considered as well.

Font styles to use
Serif
Sans Serif
Decorative

Colors
ec1f27
ffffff
000000

Requirements
Must have
• Space for employee's name, title, phone number and email address, along with the company address and website somewhere.

```html
<!DOCTYPE html>
<html lang="en">
<head>
<meta charset="utf-8">
<title>Brindle Auto – Business Card</title>
<link href="https://fonts.googleapis.com/css2?family=Roboto:wght@400;500&family=Roboto+Condensed:wght@500&display=swap" rel="stylesheet">
<style>
  :root {
    --backdrop: #2b2b2b;
    --card-white: #f2f2f2;
    --brand-red: #9b1d21;
    --frame-grey: #555555;
    --text-grey: #4a4a4a;
    --white: #ffffff;
  }
  * { margin: 0; padding: 0; box-sizing: border-box; }
  html, body {
    width: 1200px; height: 960px; overflow: hidden;
    background: var(--backdrop);
    font-family: "Roboto", Arial, sans-serif;
  }
  .canvas { position: relative; width: 1200px; height: 960px; }
  .card {
    position: absolute; width: 600px; height: 343px; overflow: hidden;
    box-shadow: 0 2px 6px rgba(0,0,0,.5);
  }
  .card-front { left: 314px; top: 113px; background: var(--card-white); }
  .card-back { left: 311px; top: 472px; background: var(--brand-red); }

  .brand-block { position: absolute; left: 35px; top: 120px; display: flex; align-items: center; gap: 10px; }
  .brand-square { width: 14px; height: 14px; background: var(--brand-red); }
  .brand-name { font-size: 20px; font-weight: 500; color: var(--frame-grey); letter-spacing: .5px; }

  .person { position: absolute; left: 44px; top: 262px; }
  .person-name { font-family: "Roboto Condensed", Arial, sans-serif; font-weight: 500; font-size: 22px; color: var(--brand-red); }
  .person-title { font-size: 15px; color: var(--text-grey); margin-top: 3px; }

  .contact-panel { position: absolute; left: 0; top: 0; }
  .contact-list {
    position: absolute; right: 38px; top: 172px; text-align: right;
    color: var(--white); font-size: 14.5px; line-height: 18px;
  }
  .address { margin-bottom: 10px; }
  .contact-row { display: flex; justify-content: flex-end; align-items: center; gap: 8px; height: 19.3px; }
  .contact-row svg { width: 13px; height: 13px; fill: var(--white); }

  .back-brand {
    position: absolute; left: 0; right: 0; top: 130px; text-align: center;
    color: var(--white); font-size: 42px; font-weight: 500; letter-spacing: 1px;
  }
  .back-web {
    position: absolute; left: 0; right: 0; top: 296px; text-align: center;
    color: var(--white); font-size: 14px; letter-spacing: 5px;
  }
</style>
</head>
<body>
<main class="canvas">
  <section class="card card-front">
    <svg class="contact-panel" width="600" height="343" viewBox="0 0 600 343">
      <path d="M296,343 L296,200 Q296,180 314,170 L430,108 Q450,98 470,108 L600,166" fill="none" stroke="var(--frame-grey)" stroke-width="5"/>
      <path d="M306,343 L306,205 Q306,188 322,179 L432,120 Q450,111 468,120 L600,180 L600,343 Z" fill="var(--brand-red)"/>
    </svg>

    <div class="brand-block">
      <span class="brand-square"></span>
      <span class="brand-name">Brindle Auto Ltd.</span>
    </div>

    <div class="person">
      <div class="person-name">MARA QUILL</div>
      <div class="person-title">CEO/FOUNDER</div>
    </div>

    <div class="contact-list">
      <div class="address">4120 Larkspur Road<br>Fairbanks, Alaska 99709</div>
      <div class="contact-row">907 555 0142
        <svg viewBox="0 0 16 16"><path d="M3 1l3 3-2 2c1 2 3 4 5 5l2-2 3 3-2 3C6 14 2 10 1 3z"/></svg></div>
      <div class="contact-row">907 555 0187
        <svg viewBox="0 0 16 16"><path d="M4 0h8v16H4z M5.5 2v10h5V2z M7 13.5h2v1H7z" fill-rule="evenodd"/></svg></div>
      <div class="contact-row">907 555 0163
        <svg viewBox="0 0 16 16"><path d="M4 1h8v4H4z M1 6h14v7h-3v2H4v-2H1z M5 10v4h6v-4z" fill-rule="evenodd"/></svg></div>
      <div class="contact-row">mara@brindleauto.com
        <svg viewBox="0 0 16 16"><path d="M1 3h14v10H1z M2 4l6 5 6-5v-.5H2z" fill-rule="evenodd"/></svg></div>
      <div class="contact-row">www.brindleauto.com
        <svg viewBox="0 0 16 16"><circle cx="8" cy="8" r="7"/><path d="M8 1v14M1 8h14" stroke="var(--brand-red)" stroke-width="1.2" fill="none"/></svg></div>
    </div>
  </section>

  <section class="card card-back">
    <div class="back-brand">Brindle Auto</div>
    <div class="back-web">www.brindleauto.com</div>
  </section>
</main>
</body>
</html>
```